Business Cards Design for the electrical wholesaler: clean bold dynamic :)

We need a business card design that would follow our latest brand guidelines. As an electrical wholesaler we want to bring a fresh look and feel into the industry. The design should be clean bold and dynamic. It should come alive with the renewed energy of our green colour. Our grey colour should keep things balanced and complement the notion of maturity and responsibility. We employ Lato as a corporate font however are not bound by this font and we’re open to interpretation here.

Target Market(s)

Electrical contractors

Industry/Entity Type

Business

Contact Information for Business Card

Logo
Name & Surname: Halyna Dorosh
Job Title: Director of Marketing
Email: halya.dorosh@quillmail.example
Cell phone: XXX.XXX.XXXX
Address: 20517 - 87 Ave. Edmonton, AB, Canada. T6K 4N8
Business Phone: 780.555.0184
Website: www.brovix.example

Font styles to use
Other font styles liked:
• Lato

Requirements
Must have
• Logo & website
Nice to have
• Brand elements - some of them you may find in the attached Brand Guidelines (e.g. three lines on the background signifying "W")

```html
<!DOCTYPE html>
<html lang="en">
<head>
<meta charset="utf-8">
<title>Brovix Business Card</title>
<link rel="stylesheet" href="https://fonts.googleapis.com/css2?family=Exo+2:wght@600&family=Roboto:wght@400;500&display=swap">
<style>
  :root {
    --backdrop: #c4c4c4;
    --charcoal: #3f4246;
    --charcoal-deep: #35383c;
    --green: #76b82a;
    --paper: #f1f1f1;
    --white: #ffffff;
    --ink-soft: #e9f3dc;
  }
  * { margin: 0; padding: 0; box-sizing: border-box; }
  html, body { width: 1200px; height: 576px; overflow: hidden; }
  body {
    background: var(--backdrop);
    font-family: "Roboto", Arial, sans-serif;
    position: relative;
  }
  .card {
    position: absolute;
    top: 138px;
    height: 294px;
    border-radius: 12px;
    overflow: hidden;
  }
  .card-front {
    left: 82px;
    width: 484px;
    background: var(--charcoal);
    display: flex;
    align-items: center;
    justify-content: center;
  }
  .wordmark {
    font-family: "Roboto", Arial, sans-serif;
    font-weight: 500;
    letter-spacing: 0.5px;
    line-height: 1;
  }
  .card-front .wordmark {
    color: var(--white);
    font-size: 50px;
    display: flex;
    align-items: center;
    gap: 12px;
  }
  .brand-square {
    width: 30px;
    height: 30px;
    background: var(--green);
    border-radius: 3px;
  }
  .card-back {
    left: 602px;
    width: 482px;
    background: var(--paper);
  }
  .card-back .panel-art {
    position: absolute;
    inset: 0;
  }
  .holder {
    position: absolute;
    left: 27px;
    top: 22px;
    color: var(--white);
  }
  .holder-name {
    font-family: "Exo 2", Arial, sans-serif;
    font-weight: 600;
    font-size: 22px;
    line-height: 1.1;
  }
  .holder-title {
    font-size: 12px;
    margin-top: 3px;
  }
  .contact {
    position: absolute;
    left: 27px;
    top: 176px;
    color: var(--ink-soft);
    font-size: 12px;
    line-height: 1.45;
  }
  .contact-lines {
    margin-top: 7px;
    display: flex;
    flex-direction: column;
    gap: 2px;
  }
  .contact-row {
    display: flex;
    align-items: center;
    gap: 6px;
  }
  .contact-icon {
    width: 13px;
    height: 13px;
    flex: none;
  }
  .card-back .wordmark {
    position: absolute;
    left: 308px;
    width: 156px;
    top: 124px;
    text-align: center;
    color: var(--charcoal);
    font-size: 44px;
  }
</style>
</head>
<body>

  <section class="card card-front" aria-label="Card front">
    <div class="wordmark"><span class="brand-square"></span>brovix</div>
  </section>

  <section class="card card-back" aria-label="Card back">
    <svg class="panel-art" width="482" height="294" viewBox="0 0 482 294" aria-hidden="true">
      <path d="M0 0 H306 C258 80 256 215 296 294 H0 Z" fill="var(--charcoal-deep)"/>
      <path d="M0 0 H296 C248 80 246 215 286 294 H0 Z" fill="var(--green)"/>
    </svg>

    <div class="holder">
      <p class="holder-name">Halyna Dorosh</p>
      <p class="holder-title">Director of Marketing</p>
    </div>

    <div class="contact">
      <p>20517 - 87 Ave. Edmonton,<br>AB, Canada. T6K 4N8</p>
      <div class="contact-lines">
        <div class="contact-row">
          <svg class="contact-icon" viewBox="0 0 14 14" aria-hidden="true"><circle cx="7" cy="7" r="6.2" fill="none" stroke="currentColor" stroke-width="1"/><path d="M4.3 5.8 q2.7-2 5.4 0 v1 h-1.4 v-0.6 q-1.3-0.5-2.6 0 v0.6 H4.3 Z M5 8 h4 v1.6 H5 Z" fill="currentColor"/></svg>
          <span>780.555.0184</span>
        </div>
        <div class="contact-row">
          <svg class="contact-icon" viewBox="0 0 14 14" aria-hidden="true"><circle cx="7" cy="7" r="6.2" fill="none" stroke="currentColor" stroke-width="1"/><rect x="4" y="4.8" width="6" height="4.4" fill="none" stroke="currentColor" stroke-width="0.9"/><path d="M4 4.8 L7 7.2 L10 4.8" fill="none" stroke="currentColor" stroke-width="0.9"/></svg>
          <span>halya.dorosh@quillmail.example</span>
        </div>
        <div class="contact-row">
          <svg class="contact-icon" viewBox="0 0 14 14" aria-hidden="true"><circle cx="7" cy="7" r="6.2" fill="none" stroke="currentColor" stroke-width="1"/><circle cx="7" cy="7" r="3.2" fill="none" stroke="currentColor" stroke-width="0.9"/><path d="M3.8 7 H10.2 M7 3.8 V10.2" stroke="currentColor" stroke-width="0.8"/></svg>
          <span>www.brovix.example</span>
        </div>
      </div>
    </div>

    <div class="wordmark">brovix</div>
  </section>

</body>
</html>
```